Website Design for The Elder Nook

Please design and code a new website.
Here are the sites I like best:
http://www.voyaglint.com/alternate/
http://www.wheelgiftbay.org
Please make it similar but look at the competitor site (below) for images and wording. This is NOT a car donation site. It's a senior lead placement site like https://www.kinhavenfinder.com. I just like this sites above as a lead generation sites.
Competitor site:
https://www.kinhavenfinder.com (use ideas / verbiage from this site)
Updates
Competitor site:
Coding
Coded - Design and coding required
Number of Pages Required
1 page
Look and feel
Each slider illustrates characteristics of the customer's brand and the style your logo design should communicate.

```html
<!DOCTYPE html>
<html lang="en">
<head>
<meta charset="utf-8">
<title>The Elder Nook – Find Senior Living Near You</title>
<link href="https://fonts.googleapis.com/css2?family=Source+Sans+3:ital,wght@0,400;0,600;0,700;0,800;1,600;1,700&display=swap" rel="stylesheet">
<style>
:root{
  --navy:#0f2f57;
  --navy-deep:#0b2445;
  --green:#1ec38b;
  --green-light:#35d6a6;
  --ink:#1d2433;
  --muted:#5a6273;
  --pale:#f3f8fc;
  --lilac:#efeefb;
  --mint:#ecf9fb;
  --white:#ffffff;
  --line:#d7dde6;
}
*{box-sizing:border-box;margin:0;padding:0}
html,body{width:1200px;height:4235px;overflow:hidden}
body{font-family:"Source Sans 3",Arial,sans-serif;color:var(--ink);background:var(--white);position:relative}
section,header,footer{position:absolute;left:0;width:1200px}
.accent{color:var(--green)}
.section-title{position:absolute;left:0;width:1200px;text-align:center;font-size:36px;font-weight:700;color:var(--navy)}

/* header */
.site-header{top:0;height:152px;background:var(--white)}
.brand{position:absolute;left:40px;top:40px;display:flex;align-items:center;gap:12px}
.brand-mark{width:34px;height:34px;border-radius:50%;background:var(--green)}
.brand-name{font-size:34px;font-weight:600;color:var(--navy);line-height:1}
.brand-tag{position:absolute;left:86px;top:80px;font-size:10px;letter-spacing:.6px;color:var(--muted);white-space:nowrap}
.header-phone{position:absolute;right:60px;top:36px;display:flex;align-items:center;gap:12px}
.phone-badge{width:56px;height:56px;border-radius:50%;border:3px solid var(--navy);display:flex;align-items:center;justify-content:center}
.header-phone strong{display:block;font-size:32px;font-weight:800;color:var(--navy);line-height:1}
.header-phone small{font-size:13px;color:var(--navy)}

.main-nav{position:absolute;left:0;top:152px;width:1200px;height:40px;background:var(--navy);display:flex;align-items:center;padding-left:18px;gap:24px;font-size:14px;font-weight:700;color:var(--white);text-transform:uppercase}
.nav-home{width:24px;height:24px;background:var(--green);display:flex;align-items:center;justify-content:center}

/* hero */
.hero{top:192px;height:513px}
.hero-photo{position:absolute;inset:0;background:linear-gradient(110deg,#6d7f5f 0%,#a6ae8e 35%,#c9c6b4 55%,#8c8f7c 80%,#5d6652 100%)}
.hero-title{position:absolute;left:150px;top:180px;width:560px;text-align:center;font-size:44px;font-weight:700;line-height:1.08;color:var(--white);text-shadow:0 2px 8px rgba(0,0,0,.45)}
.contact-head{position:absolute;left:768px;top:124px;width:378px;height:74px;background:var(--green);color:var(--white);font-size:30px;font-weight:700;display:flex;align-items:center;justify-content:center}
.lead-form{position:absolute;left:768px;top:6px;width:378px;height:340px;background:rgba(15,47,87,.88);padding:28px 26px;display:grid;grid-template-columns:1fr 1fr;gap:14px 12px;align-content:start}
.field{height:48px;background:var(--white);font-size:15px;font-weight:700;color:var(--ink);padding:0 12px;display:flex;align-items:center;justify-content:space-between}
.field.wide{grid-column:1/3}
.req{color:#d23}
.submit{width:120px;height:44px;background:var(--green);color:var(--white);font-weight:700;font-size:15px;display:flex;align-items:center;justify-content:center;text-transform:uppercase}

/* support band */
.support{top:705px;height:193px;background:linear-gradient(90deg,var(--green) 0%,var(--green-light) 100%)}
.support-badge{position:absolute;left:56px;top:-6px;width:466px;height:205px}
.support-badge span{position:absolute;left:0;top:0;width:466px;height:205px;display:flex;flex-direction:column;align-items:center;justify-content:center;color:var(--white);font-weight:800;font-size:31px;line-height:1.15;text-align:center}
.support-badge span b{font-size:40px}
.support-items{position:absolute;left:520px;top:42px;width:670px;display:flex;justify-content:space-between}
.support-item{width:124px;text-align:center;color:var(--white);font-size:14px;font-weight:700;line-height:1.2}
.support-item svg{display:block;margin:0 auto 12px}

/* steps */
.steps{top:898px;height:593px;background:var(--pale)}
.steps .section-title{top:118px}
.step{position:absolute;top:200px;width:260px;text-align:center}
.step-photo{width:176px;height:176px;margin:0 auto;border-radius:50%;border:8px solid var(--white);box-shadow:0 4px 16px rgba(0,0,0,.12)}
.step-num{margin-top:18px;font-size:28px;font-weight:700;color:var(--navy)}
.step-num.accent{color:var(--green)}
.step-text{font-size:22px;font-weight:600;color:var(--ink);line-height:1.2}

/* no cost */
.nocost{top:1491px;height:438px;background:var(--pale)}
.nocost-photo{position:absolute;left:0;top:0;width:940px;height:438px;background:linear-gradient(90deg,#d9c7b6 0%,#efe3d9 40%,#f1ece8 70%,rgba(243,248,252,0) 100%)}
.nocost-copy{position:absolute;left:686px;top:80px;width:440px}
.nocost-copy h2{font-size:42px;font-weight:800;color:var(--navy)}
.nocost-copy p{margin-top:14px;padding-left:18px;font-size:20px;font-weight:700;line-height:1.3;color:var(--ink);text-align:center}
.call-btn{margin:26px 0 0 44px;width:334px;height:70px;background:var(--green);color:var(--white);font-size:34px;font-weight:700;display:flex;align-items:center;justify-content:center;border-radius:3px}

/* testimonials */
.reviews{top:1929px;height:706px;background:var(--white)}
.reviews .section-title{top:88px}
.quote{position:absolute;width:508px;padding:24px 34px;font-size:16px;line-height:1.35;color:var(--ink)}
.quote.one{left:94px;top:176px;background:var(--lilac)}
.quote.two{left:594px;top:234px;background:var(--mint)}
.reviewer{position:absolute;display:flex;align-items:center;gap:22px;font-size:21px;font-weight:700;font-style:italic;color:var(--navy)}
.reviewer i{display:block;width:92px;height:92px;border-radius:50%;border:5px solid var(--white);box-shadow:0 2px 10px rgba(0,0,0,.15)}
.dots{position:absolute;left:560px;top:594px;display:flex;gap:8px}
.dots i{width:13px;height:13px;border-radius:50%;border:1px solid #b6bdc8;background:var(--white)}
.dots i:first-child{background:#b6bdc8}

/* advisor */
.advisor{top:2635px;height:494px}
.advisor-photo{position:absolute;inset:0;background:linear-gradient(180deg,#c4d8ee 0%,#dfe9f4 55%,#a9c1de 100%)}
.advisor-copy{position:absolute;left:72px;top:92px;width:480px}
.advisor-copy h2{font-size:38px;font-weight:800;line-height:1.1;color:var(--navy)}
.advisor-copy p{margin-top:18px;font-size:20px;font-weight:700;line-height:1.3;color:var(--ink)}
.perks{margin-top:18px;list-style:none}
.perks li{display:flex;align-items:center;gap:16px;font-size:20px;font-weight:700;color:var(--navy);margin-bottom:15px}

/* states */
.states{top:3129px;height:641px;background:var(--pale)}
.states .section-title{top:96px}
.tabs{position:absolute;left:93px;top:172px;width:274px}
.tab{height:50px;margin-bottom:12px;background:var(--white);display:flex;align-items:center;font-size:21px;font-weight:700;color:var(--navy);box-shadow:0 2px 6px rgba(0,0,0,.08)}
.tab b{width:40px;height:40px;margin:0 14px 0 5px;background:var(--navy);display:flex;align-items:center;justify-content:center}
.tab.active{color:var(--green)}
.tab.active b{background:var(--green)}
.tab.active::after{content:"";margin-left:auto;margin-right:14px;border:8px solid transparent;border-right:10px solid var(--navy)}
.state-col{position:absolute;top:186px;list-style:none;font-size:17px;line-height:23px;color:var(--ink)}

/* footer */
.site-footer{top:3770px;height:404px;background:linear-gradient(180deg,#173f6b 0%,#0f3158 100%)}
.footer-brand{position:absolute;left:0;width:1200px;top:50px;text-align:center;color:var(--white)}
.footer-brand .brand-name{color:var(--white);font-size:32px}
.footer-brand small{display:block;margin-top:8px;font-size:10px;letter-spacing:.6px}
.footer-col{position:absolute;top:180px;color:var(--white)}
.footer-col h3{font-size:14px;font-weight:700;color:var(--green);text-transform:uppercase;padding-bottom:10px;border-bottom:1px solid rgba(255,255,255,.3);width:200px}
.footer-col p,.footer-col li{font-size:13px;font-weight:700;line-height:1.35;list-style:none}
.footer-col p{margin-top:18px;width:220px}
.footer-col ul{margin-top:18px}
.footer-phone{position:absolute;left:736px;top:176px;display:flex;align-items:center;gap:12px;color:var(--white)}
.footer-phone .phone-badge{border-color:var(--white);width:52px;height:52px}
.footer-phone strong{display:block;font-size:28px;font-weight:800;color:var(--green);line-height:1}
.footer-phone small{font-size:11px}
.social{position:absolute;left:812px;top:262px;display:flex;gap:8px}
.social i{width:28px;height:28px;border-radius:3px;background:#3b6fd8}
.copyright{position:absolute;left:0;top:4174px;width:1200px;height:61px;background:var(--white);display:flex;align-items:center;justify-content:center;font-size:13px;font-weight:700;color:var(--ink)}
</style>
</head>
<body>

<header class="site-header">
  <div class="brand"><span class="brand-mark"></span><span class="brand-name">The Elder Nook</span></div>
  <div class="brand-tag">CONNECTING FAMILIES TO SENIOR LIVING</div>
  <div class="header-phone">
    <span class="phone-badge"><svg width="28" height="28" viewBox="0 0 24 24"><path fill="#0f2f57" d="M6.6 10.8a15 15 0 0 0 6.6 6.6l2.2-2.2c.3-.3.7-.4 1-.2 1.1.4 2.3.6 3.6.6.6 0 1 .4 1 1V20c0 .6-.4 1-1 1A17 17 0 0 1 3 4c0-.6.4-1 1-1h3.5c.6 0 1 .4 1 1 0 1.3.2 2.5.6 3.6.1.3 0 .7-.2 1z"/></svg></span>
    <div><strong>1-800-555-0142</strong><small>Talk Today to a Local Advisor for FREE</small></div>
  </div>
  <div class="contact-head">Contact us now!</div>
</header>

<nav class="main-nav">
  <span class="nav-home"><svg width="14" height="14" viewBox="0 0 24 24"><path fill="#fff" d="M12 3l10 9h-3v9h-5v-6h-4v6H5v-9H2z"/></svg></span>
  <span>Assisted Living</span><span>Memory Care</span><span>Nursing Homes</span><span>More Living Options ▾</span><span>Planning &amp; Advice</span>
</nav>

<section class="hero">
  <div class="hero-photo" role="img" aria-label="Photo of two smiling seniors walking together in a leafy park"></div>
  <h1 class="hero-title">You know your family.<br>We know Senior Living.<br>Find Senior Living Near You.</h1>
  <form class="lead-form">
    <div class="field">First Name<span class="req">*</span></div>
    <div class="field">Last Name<span class="req">*</span></div>
    <div class="field">Primary Phone<span class="req">*</span></div>
    <div class="field">Cell Phone<span class="req">*</span></div>
    <div class="field wide">Email Address<span class="req">*</span></div>
    <div class="field wide">State<span class="req">*</span><span>▼</span></div>
    <div class="submit">Submit</div>
  </form>
</section>

<section class="support">
  <div class="support-badge">
    <svg width="466" height="205" viewBox="0 0 466 205"><polygon points="34,0 432,0 466,102 432,205 34,205 0,102" fill="#0f2f57"/></svg>
    <span>THE SUPPORT YOU<br>NEED TO MAKE THE<b>RIGHT CHOICE</b></span>
  </div>
  <div class="support-items">
    <div class="support-item"><svg width="52" height="52" viewBox="0 0 52 52" fill="none" stroke="#fff" stroke-width="3"><circle cx="26" cy="16" r="9"/><path d="M10 46c0-10 7-16 16-16s16 6 16 16"/></svg>Dedicated local advisor</div>
    <div class="support-item"><svg width="52" height="52" viewBox="0 0 52 52" fill="none" stroke="#fff" stroke-width="3"><rect x="8" y="16" width="36" height="30"/><path d="M4 18L26 5l22 13"/><rect x="21" y="32" width="10" height="14"/></svg>Hand-picked list of communities</div>
    <div class="support-item"><svg width="52" height="52" viewBox="0 0 52 52" fill="none" stroke="#fff" stroke-width="3"><rect x="11" y="5" width="30" height="42"/><path d="M26 14v22M31 18h-7a3 3 0 0 0 0 6h4a3 3 0 0 1 0 6h-7"/></svg>Full details and pricing</div>
    <div class="support-item"><svg width="52" height="52" viewBox="0 0 52 52" fill="none" stroke="#fff" stroke-width="3"><rect x="7" y="10" width="38" height="36"/><path d="M7 20h38M16 5v9M36 5v9M15 28h6M25 28h6M35 28h4M15 37h6M25 37h6"/></svg>Help scheduling tours</div>
    <div class="support-item"><svg width="52" height="52" viewBox="0 0 52 52" fill="none" stroke="#fff" stroke-width="3"><path d="M4 16h28v20H4zM32 22h9l7 8v6H32z"/><circle cx="13" cy="39" r="4"/><circle cx="40" cy="39" r="4"/></svg>Move in support</div>
  </div>
</section>

<section class="steps">
  <h2 class="section-title">How Our <span class="accent">Service Works</span></h2>
  <div class="step" style="left:62px"><div class="step-photo" role="img" aria-label="Photo of a friendly advisor wearing a headset" style="background:linear-gradient(160deg,#f1dcc8,#c9a486)"></div><div class="step-num">01.</div><div class="step-text">Talk with your<br>local advisor</div></div>
  <div class="step" style="left:322px"><div class="step-photo" role="img" aria-label="Photo of a caregiver talking with a senior woman" style="background:linear-gradient(160deg,#e6d3c6,#b69383)"></div><div class="step-num accent">02.</div><div class="step-text">Get information<br>on care options</div></div>
  <div class="step" style="left:604px"><div class="step-photo" role="img" aria-label="Photo of a family visiting a senior community" style="background:linear-gradient(160deg,#bfcfc4,#6e8578)"></div><div class="step-num">03.</div><div class="step-text">Select communities<br>to visit</div></div>
  <div class="step" style="left:875px"><div class="step-photo" role="img" aria-label="Photo of a grandfather and grandson at home" style="background:linear-gradient(160deg,#c8d0da,#7d8896)"></div><div class="step-num accent">04.</div><div class="step-text">Transition to<br>new home</div></div>
</section>

<section class="nocost">
  <div class="nocost-photo" role="img" aria-label="Photo of a young caregiver hugging a smiling senior woman"></div>
  <div class="nocost-copy">
    <h2>There's <span class="accent">No Cost</span> to You</h2>
    <p>We work with over 20,000 senior living communities. Our community partners pay us for placement services.</p>
    <div class="call-btn">Call 800-555-0142</div>
  </div>
</section>

<section class="reviews">
  <h2 class="section-title">97% of Our Customers <span class="accent">Recommend Our Service</span></h2>
  <p class="quote one">Lorem ipsum dolor sit amet, consectetur adipiscing elit, sed do eiusmod tempor incididunt ut labore et dolore magna aliqua. Ut enim ad minim veniam, quis nostrud exercitation ullamco laboris nisi ut aliquip ex. Duis aute irure dolor in reprehenderit in voluptate velit esse.</p>
  <div class="reviewer" style="left:100px;top:386px"><i role="img" aria-label="Portrait of the reviewer" style="background:linear-gradient(160deg,#e4cbb8,#8a6a58)"></i>Margaret Ellison</div>
  <p class="quote two">Lorem ipsum dolor sit amet, consectetur adipiscing elit, sed do eiusmod tempor incididunt ut labore et dolore magna aliqua. Ut enim ad minim veniam, quis nostrud exercitation ullamco laboris nisi ut aliquip ex. Duis aute irure dolor in reprehenderit in voluptate velit esse.</p>
  <div class="reviewer" style="left:606px;top:440px"><i role="img" aria-label="Portrait of the reviewer" style="background:linear-gradient(160deg,#efdccb,#c4a68c)"></i>Joan Whitaker</div>
  <div class="dots"><i></i><i></i><i></i><i></i></div>
</section>

<section class="advisor">
  <div class="advisor-photo" role="img" aria-label="Photo of a joyful senior man with arms spread wide under a bright sky"></div>
  <div class="advisor-copy">
    <h2>Your local advisor.<br><span class="accent">You decide.</span></h2>
    <p>Over 400 senior advisors across the U.S. and Canada are ready to help your family with:</p>
    <ul class="perks">
      <li><svg width="24" height="26" viewBox="0 0 24 26" fill="none" stroke="#0f2f57" stroke-width="2.4"><path d="M12 24s-8-8-8-14a8 8 0 0 1 16 0c0 6-8 14-8 14z"/><circle cx="12" cy="10" r="3"/></svg>Insider's tips for the area near you</li>
      <li><svg width="24" height="24" viewBox="0 0 24 24" fill="none" stroke="#0f2f57" stroke-width="2.2"><circle cx="9" cy="8" r="4"/><path d="M2 22c0-5 3-8 7-8s7 3 7 8M16 4h6v5h-4l-2 2z"/></svg>Advice tailored to your unique situation</li>
      <li><svg width="24" height="24" viewBox="0 0 24 24" fill="none" stroke="#0f2f57" stroke-width="2.2"><circle cx="12" cy="12" r="10"/><path d="M12 11v6M12 7v1"/></svg>Time saving know-how and resources</li>
    </ul>
  </div>
</section>

<section class="states">
  <h2 class="section-title">Senior Living <span class="accent">by State</span></h2>
  <div class="tabs">
    <div class="tab active"><b><svg width="22" height="22" viewBox="0 0 24 24" fill="#fff"><circle cx="7" cy="4" r="2.5"/><circle cx="17" cy="4" r="2.5"/><path d="M4 8h6v8H8v6H6v-6H4zM14 8h6v8h-2v6h-2v-6h-2z"/></svg></b>Assisted Living</div>
    <div class="tab"><b><svg width="22" height="22" viewBox="0 0 24 24" fill="none" stroke="#fff" stroke-width="2"><circle cx="12" cy="12" r="8"/><path d="M9 10a3 3 0 0 1 6 0c0 3-3 2-3 5"/></svg></b>Memory Care</div>
    <div class="tab"><b><svg width="22" height="22" viewBox="0 0 24 24" fill="#fff"><circle cx="12" cy="4" r="2.5"/><path d="M10 8h4l1 7h-2l-1 7h-1l-1-7H8z"/></svg></b>Independent Living</div>
    <div class="tab"><b><svg width="22" height="22" viewBox="0 0 24 24" fill="#fff"><path d="M12 3l10 8h-3v10H5V11H2z"/></svg></b>Nursing Home</div>
    <div class="tab"><b><svg width="22" height="22" viewBox="0 0 24 24" fill="none" stroke="#fff" stroke-width="2"><path d="M12 20s-8-5-8-11a4 4 0 0 1 8-1 4 4 0 0 1 8 1c0 6-8 11-8 11z"/></svg></b>Care Homes</div>
  </div>
  <ul class="state-col" style="left:446px"><li>Alabama</li><li>Arizona</li><li>Arkansas</li><li>California</li><li>Colorado</li><li>Connecticut</li><li>Delaware</li><li>District of Columbia</li><li>Florida</li><li>Georgia</li><li>Hawaii</li><li>Idaho</li><li>Illinois</li><li>Indiana</li><li>Iowa</li><li>Kansas</li><li>Kentucky</li></ul>
  <ul class="state-col" style="left:697px"><li>Louisiana</li><li>Maine</li><li>Maryland</li><li>Massachusetts</li><li>Michigan</li><li>Minnesota</li><li>Mississippi</li><li>Missouri</li><li>Montana</li><li>Nebraska</li><li>Nevada</li><li>New Hampshire</li><li>New Jersey</li><li>New Mexico</li><li>New York</li><li>North Carolina</li><li>North Dakota</li></ul>
  <ul class="state-col" style="left:906px"><li>Ohio</li><li>Oklahoma</li><li>Oregon</li><li>Pennsylvania</li><li>Rhode Island</li><li>South Carolina</li><li>South Dakota</li><li>Tennessee</li><li>Texas</li><li>Utah</li><li>Vermont</li><li>Virginia</li><li>Washington</li><li>West Virginia</li><li>Wisconsin</li><li>Wyoming</li></ul>
</section>

<footer class="site-footer">
  <div class="footer-brand"><span class="brand-name">The Elder Nook</span><small>CONNECTING FAMILIES TO SENIOR LIVING</small></div>
  <div class="footer-col" style="left:206px">
    <h3>About The Elder Nook</h3>
    <p>We guide families toward caring senior living choices with local advisors, honest details and free support from first call to move in.</p>
  </div>
  <div class="footer-col" style="left:506px">
    <h3>Quick Links</h3>
    <ul><li>Assisted Living</li><li>Memory Care</li><li>Nursing Home</li><li>More Living Options</li><li>Planning &amp; Advice</li><li>How Our Service Works</li></ul>
  </div>
  <div class="footer-phone">
    <span class="phone-badge"><svg width="24" height="24" viewBox="0 0 24 24"><path fill="#fff" d="M6.6 10.8a15 15 0 0 0 6.6 6.6l2.2-2.2c.3-.3.7-.4 1-.2 1.1.4 2.3.6 3.6.6.6 0 1 .4 1 1V20c0 .6-.4 1-1 1A17 17 0 0 1 3 4c0-.6.4-1 1-1h3.5c.6 0 1 .4 1 1 0 1.3.2 2.5.6 3.6.1.3 0 .7-.2 1z"/></svg></span>
    <div><strong>1-800-555-0142</strong><small>Talk Today to a Local Advisor for FREE</small></div>
  </div>
  <div class="social"><i></i><i></i><i></i></div>
</footer>
<div class="copyright">COPYRIGHT © 2019 THE ELDER NOOK. ALL RIGHTS RESERVED.</div>

</body>
</html>
```